Halvor Grading and Septic needs a flyer to submit to contractors to offer our services

I need a sleek profession one page full color high gloss document showcasing our services to give to Mobile Home Companies and contractors that need our services.

Target Market(s)

Home Builders. Mobile Home Salesmen. People Building new homes.

Industry/Entity Type

Construction

Font styles to use
Serif
Sans Serif

Requirements
Must have
• Phone Number. Email address. Logo. Services offered: Mobile Home Pads, Meter Pole Placement and Connection, Waterline Connection, On Site Septic System Installs
Should not have
• Jokes, Nothing trying to be cute

```html
<!DOCTYPE html>
<html lang="en">
<head>
<meta charset="utf-8">
<title>Halvor Grading and Septic – Services Flyer</title>
<link rel="stylesheet" href="https://fonts.googleapis.com/css2?family=Montserrat:wght@600;700&family=Poppins:ital,wght@0,700;1,500;1,600;1,700;1,800;1,900&display=swap">
<style>
  :root{
    --navy:#1c4f8b;
    --navy-deep:#163e70;
    --red:#c9202a;
    --white:#ffffff;
    --ink:#1d1d22;
    --mist:#eceef1;
    --rule:#7f9cc0;
  }
  *{margin:0;padding:0;box-sizing:border-box}
  html,body{width:803px;height:1200px;overflow:hidden;background:var(--white)}
  .flyer{position:relative;width:803px;height:1200px;overflow:hidden;
    background:linear-gradient(180deg,#fff 0%,#f4f5f7 45%,var(--mist) 100%);
    font-family:'Poppins',sans-serif}
  .layer{position:absolute;left:0;top:0}
  .brand{position:absolute;left:40px;top:44px;display:flex;align-items:center;gap:12px}
  .brand-dot{width:22px;height:22px;border-radius:50%;background:var(--navy)}
  .brand-name{font-family:'Poppins',sans-serif;font-weight:700;color:var(--navy);
    font-size:25px;line-height:1.05;text-transform:uppercase;letter-spacing:.5px}
  .headline{position:absolute;left:0;width:803px;text-align:center;top:198px;
    font-style:italic;font-weight:900;text-transform:uppercase;line-height:1}
  .headline span{display:block}
  .headline .h-top{color:var(--white);font-size:44px;letter-spacing:1px}
  .headline .h-mid{color:var(--red);font-size:72px;margin-top:2px;letter-spacing:1px}
  .headline .h-bot{color:var(--white);font-size:54px;margin-top:0;letter-spacing:1px}
  .intro{position:absolute;left:120px;width:520px;top:420px;text-align:center;color:var(--white);font-style:italic}
  .intro p{font-size:14.5px;font-weight:600;line-height:1.25}
  .intro .cta{font-size:21px;font-weight:500;margin-top:12px}
  .services-title{position:absolute;left:216px;top:564px;width:372px;height:40px;border-radius:20px;
    background:var(--navy);color:var(--white);text-align:center;font-style:italic;font-weight:700;
    font-size:30px;line-height:40px}
  .service{position:absolute;width:340px;text-align:center;font-family:'Montserrat',sans-serif;
    font-weight:700;font-size:19.5px;line-height:1.32;color:var(--ink);text-transform:uppercase}
  .email{position:absolute;left:44px;top:1126px;width:400px;text-align:center;color:var(--white);
    font-style:italic;font-weight:700;font-size:17.5px}
  .phone{position:absolute;left:490px;top:1108px;width:300px;text-align:center;color:var(--white);
    font-style:italic;font-weight:800;font-size:35px}
</style>
</head>
<body>
<main class="flyer">

  <svg class="layer" width="803" height="1200" viewBox="0 0 803 1200" aria-hidden="true">
    <defs>
      <linearGradient id="heroTone" x1="0" y1="0" x2="1" y2="1">
        <stop offset="0" stop-color="#5c6e85"/>
        <stop offset=".5" stop-color="#6d7180"/>
        <stop offset="1" stop-color="#3f5e86"/>
      </linearGradient>
      <linearGradient id="tankTone" x1="0" y1="0" x2="1" y2="0">
        <stop offset="0" stop-color="#eef0f2" stop-opacity="0"/>
        <stop offset=".4" stop-color="#e3e5e8"/>
        <stop offset="1" stop-color="#b9bcc1"/>
      </linearGradient>
    </defs>

    <!-- hero photo -->
    <g role="img" aria-label="Photo of an excavator beside a freshly dug septic site with tank lids, tinted blue">
      <polygon points="0,164 337,164 372,61 803,61 803,402 0,402" fill="url(#heroTone)"/>
    </g>
    <!-- top band -->
    <polyline points="0,158 336,158 370,45 803,45" fill="none" stroke="var(--navy)" stroke-width="14"/>

    <!-- intro frame -->
    <polygon points="33,413 758,413 641,537 78,537" fill="var(--navy)"/>
    <g role="img" aria-label="Continuation of the job site photo, deep blue tint">
      <polygon points="56,418 736,418 626,525 94,525" fill="var(--navy-deep)" opacity=".85"/>
    </g>
    <polyline points="100,418 122,519 618,519 664,418" fill="none" stroke="#fff" stroke-width="2.5"/>

    <!-- faint tank photo behind lower services -->
    <g role="img" aria-label="Faded photo of a worker setting a concrete septic tank">
      <rect x="370" y="800" width="433" height="260" fill="url(#tankTone)"/>
    </g>

    <!-- service grid rules -->
    <line x1="403" y1="618" x2="403" y2="1018" stroke="var(--rule)" stroke-width="1.5"/>
    <line x1="70" y1="810" x2="392" y2="810" stroke="var(--rule)" stroke-width="1.2"/>
    <line x1="411" y1="810" x2="732" y2="810" stroke="var(--rule)" stroke-width="1.2"/>

    <!-- service icons -->
    <g>
      <circle cx="202" cy="685" r="48" fill="var(--red)"/>
      <circle cx="202" cy="685" r="41" fill="var(--navy)"/>
      <g fill="none" stroke="#fff" stroke-width="3" stroke-linejoin="round">
        <path d="M180 702 V675 L202 660 L224 675 V702 Z"/>
        <rect x="186" y="680" width="10" height="9"/>
        <rect x="205" y="680" width="11" height="22"/>
        <line x1="172" y1="702" x2="232" y2="702"/>
        <circle cx="190" cy="708" r="4"/><circle cx="200" cy="708" r="4"/>
      </g>
    </g>
    <g>
      <circle cx="549" cy="683" r="48" fill="var(--red)"/>
      <circle cx="549" cy="683" r="41" fill="var(--navy)"/>
      <g fill="none" stroke="#fff" stroke-width="3" stroke-linecap="round">
        <line x1="537" y1="662" x2="537" y2="706"/>
        <line x1="526" y1="666" x2="548" y2="666"/>
        <line x1="529" y1="674" x2="545" y2="674"/>
        <rect x="549" y="684" width="20" height="16" rx="2"/>
        <line x1="554" y1="690" x2="564" y2="690"/><line x1="554" y1="695" x2="564" y2="695"/>
        <path d="M552 668 Q562 668 562 678"/>
      </g>
    </g>
    <g>
      <circle cx="202" cy="875" r="48" fill="var(--red)"/>
      <circle cx="202" cy="875" r="41" fill="var(--navy)"/>
      <g fill="none" stroke="#fff" stroke-width="3" stroke-linejoin="round">
        <path d="M178 866 L202 852 L226 866"/>
        <path d="M188 870 H200 V890 H214 V880"/>
        <path d="M208 880 H220"/>
        <path d="M182 896 H222"/>
        <rect x="186" y="866" width="8" height="8"/>
      </g>
    </g>
    <g>
      <circle cx="549" cy="872" r="48" fill="var(--red)"/>
      <circle cx="549" cy="872" r="41" fill="var(--navy)"/>
      <g fill="#fff">
        <rect x="527" y="862" width="44" height="24" rx="5"/>
        <rect x="532" y="852" width="10" height="10"/>
        <rect x="556" y="852" width="10" height="10"/>
        <rect x="545" y="876" width="8" height="12" fill="var(--navy)"/>
      </g>
    </g>

    <!-- footer -->
    <g role="img" aria-label="Strip of photo showing ground at the tank site">
      <polygon points="450,1010 803,1010 803,1060 440,1060" fill="#8f949a" opacity=".75"/>
    </g>
    <polygon points="0,1034 803,1034 803,1052 0,1052" fill="var(--navy)"/>
    <rect x="0" y="1062" width="803" height="138" fill="var(--red)"/>
    <polygon points="478,1062 803,1062 803,1165 448,1165" fill="var(--white)"/>
    <polygon points="488,1068 803,1068 803,1158 460,1158" fill="var(--navy)"/>

    <circle cx="638" cy="1078" r="14" fill="var(--navy)" stroke="#fff" stroke-width="2"/>
    <path d="M632 1071 l4 0 l2 5 l-3 2 q2 4 6 6 l2 -3 l5 2 l0 4 q-10 1 -16 -12 z" fill="#fff"/>

    <circle cx="255" cy="1097" r="19" fill="#fff"/>
    <rect x="244" y="1089" width="22" height="16" rx="2" fill="var(--red)"/>
    <polyline points="244,1090 255,1099 266,1090" fill="none" stroke="#fff" stroke-width="2"/>
  </svg>

  <div class="brand">
    <span class="brand-dot"></span>
    <span class="brand-name">Halvor Grading<br>&amp; Septic</span>
  </div>

  <h1 class="headline">
    <span class="h-top">Professional</span>
    <span class="h-mid">Wastewater</span>
    <span class="h-bot">Management</span>
  </h1>

  <div class="intro">
    <p>Halvor Grading and Septic offers professional septic and excavation services in East Texas.</p>
    <p class="cta">Call us now for a free estimate!</p>
  </div>

  <h2 class="services-title">Services offered:</h2>

  <div class="service" style="left:27px;top:745px">Mobile<br>Home Pads</div>
  <div class="service" style="left:377px;top:745px">Meter Pole Placement<br>and Connection</div>
  <div class="service" style="left:27px;top:934px">Waterline<br>Connection</div>
  <div class="service" style="left:379px;top:934px">On Site Septic<br>System Installs</div>

  <div class="email">dana@halvorgradingandseptic.com</div>
  <div class="phone">(903) 555-0147</div>
</main>
</body>
</html>
```